Bundrova Hero Unit Icon

Bundrova (http://www.bundrova-example.com) is a "software as a service" site that lets developers create Zip files on the fly so they don't have to stress their servers. The site design is pretty much done, but I need an image to replace the one at the top of the main page, to the right of "Create Zip Files Instantly" (currently just a browser that says Spindle Harbor. It will be replaced with your image).

The new image should somehow illustrate that you can quickly Zip up any type of file (images, documents, binary files) and the output is a Zip file that is instantly ready to download.

Target Market(s)

Software developers

Industry/Entity Type

Software

Requirements
Must have
• Must work well when placed in the existing hero unit space with the green background.

Must scale well (max size is 570 x 365). The design is responsive.

```html
<!DOCTYPE html>
<html lang="en">
<head>
<meta charset="utf-8">
<title>Bundrova – Create Zip Files Instantly</title>
<link href="https://fonts.googleapis.com/css2?family=Open+Sans:wght@400;600;700&display=swap" rel="stylesheet">
<style>
  :root {
    --nav-top: #3a3a3a;
    --nav-bottom: #2c2c2c;
    --nav-active: #262626;
    --brand-green: #7b9c45;
    --accent-green: #8fae5a;
    --text-white: #ffffff;
    --text-dark: #333333;
    --text-body: #555555;
    --link-blue: #2a7ab8;
    --rule-dark: #444444;
    --page-bg: #ffffff;
  }
  * { box-sizing: border-box; margin: 0; padding: 0; }
  html, body {
    width: 1200px; height: 851px; overflow: hidden;
    background: var(--page-bg);
    font-family: "Open Sans", Arial, sans-serif;
  }
  .page { position: relative; width: 1200px; height: 851px; }

  .site-nav {
    position: absolute; left: 0; top: 0; width: 1200px; height: 64px;
    background: linear-gradient(var(--nav-top), var(--nav-bottom));
  }
  .brand {
    position: absolute; left: 44px; top: 16px;
    display: flex; align-items: center; gap: 10px;
    color: #d8d8d8; font-size: 24px; font-weight: 400;
  }
  .brand-mark { width: 28px; height: 28px; border-radius: 50%; background: var(--accent-green); }
  .nav-links { position: absolute; top: 0; left: 730px; height: 64px; display: flex; list-style: none; }
  .nav-links li {
    height: 64px; line-height: 64px; padding: 0 13px;
    color: var(--text-white); font-size: 14px; font-weight: 600;
  }
  .nav-links li:first-child { padding: 0 14px; }
  .nav-links li.active { background: var(--nav-active); color: var(--accent-green); }

  .hero {
    position: absolute; left: 0; top: 64px; width: 1200px; height: 371px;
    background: var(--brand-green);
  }
  .hero-title {
    position: absolute; left: 44px; top: 42px;
    color: var(--text-white); font-size: 35px; font-weight: 600;
    text-shadow: 0 2px 2px rgba(0,0,0,.35);
  }
  .hero-copy {
    position: absolute; left: 44px; top: 112px; width: 545px;
    color: var(--text-white); font-size: 14.5px; line-height: 28px; letter-spacing: -0.1px;
  }
  .hero-copy p + p { margin-top: 24px; }
  .hero-actions { position: absolute; left: 44px; top: 276px; display: flex; gap: 13px; }
  .btn {
    height: 46px; line-height: 46px; padding: 0 17px; border-radius: 3px;
    font-size: 17px; font-weight: 600;
  }
  .btn-primary { background: #2e2e2e; color: var(--text-white); }
  .btn-secondary { background: #f4f4f4; color: var(--text-dark); border: 1px solid #ddd; }
  .hero-art {
    position: absolute; left: 607px; top: 29px; width: 534px; height: 342px;
    background: radial-gradient(ellipse at 50% 35%, #f2f2f2, #bdbdbd 75%, #9c9c9c);
  }
  .hero-rule { position: absolute; left: 44px; top: 435px; width: 1097px; height: 3px; background: var(--rule-dark); }

  .section-title {
    position: absolute; left: 44px;
    color: var(--text-dark); font-size: 28px; font-weight: 600;
  }
  .section-title .brace { color: var(--brand-green); }
  .highlights-title { top: 485px; }
  .tryit-title { top: 710px; }

  .feature { position: absolute; top: 559px; width: 340px; }
  .feature-icon { position: absolute; left: 0; top: 0; }
  .feature-name { position: absolute; left: 64px; top: 18px; font-size: 13px; font-weight: 600; color: var(--text-dark); }
  .feature-text { position: absolute; left: 64px; top: 46px; width: 272px; font-size: 12px; line-height: 21px; color: var(--text-body); letter-spacing: -0.1px; }
  .feature-text a { color: var(--link-blue); text-decoration: none; }

  .tryit-intro { position: absolute; left: 44px; top: 774px; font-size: 12px; color: var(--text-dark); }
  .demo-frame { position: absolute; left: 44px; top: 814px; width: 1097px; height: 40px; border-top: 1px solid #ddd; }
</style>
</head>
<body>
<div class="page">
  <header class="site-nav">
    <div class="brand"><span class="brand-mark"></span>Bundrova</div>
    <ul class="nav-links">
      <li class="active">Home</li><li>Docs</li><li>Plans</li><li>Blog</li><li>Contact Us</li><li>Log In</li>
    </ul>
  </header>

  <section class="hero">
    <h1 class="hero-title">Create Zip Files Instantly</h1>
    <div class="hero-copy">
      <p>Use our API to create zip files from existing online files and let your users download them immediately. No more tying up your servers generating zip files or making your users download multiple files one at a time.</p>
      <p>Save yourself and your users the headaches. Bundrova it!</p>
    </div>
    <div class="hero-actions">
      <span class="btn btn-primary">Sign Up</span>
      <span class="btn btn-secondary">See a Demo</span>
    </div>
    <div class="hero-art" role="img" aria-label="Illustration of documents, photos, music and disc files flying into a green zip archive with a Download Now button"></div>
  </section>
  <div class="hero-rule"></div>

  <h2 class="section-title highlights-title"><span class="brace">{</span> Highlights <span class="brace">}</span></h2>

  <div class="feature" style="left:44px">
    <svg class="feature-icon" width="46" height="46" viewBox="0 0 46 46"><circle cx="23" cy="23" r="22" fill="#333"/><circle cx="23" cy="23" r="19" fill="none" stroke="#fff" stroke-width="1.5"/><circle cx="23" cy="23" r="8" fill="none" stroke="#8fae5a" stroke-width="2"/><path d="M23 18v5h4" fill="none" stroke="#8fae5a" stroke-width="2"/></svg>
    <div class="feature-name">Ready Instantly</div>
    <p class="feature-text">Your Zip file is ready for delivery as soon as you send us the file list via our API, no matter how big it is or how many files it includes. <a href="#">Try it</a>.</p>
  </div>
  <div class="feature" style="left:419px">
    <svg class="feature-icon" width="46" height="46" viewBox="0 0 46 46"><circle cx="23" cy="23" r="22" fill="#333"/><circle cx="23" cy="23" r="19" fill="none" stroke="#fff" stroke-width="1.5"/><path d="M15 31l13-13" stroke="#8fae5a" stroke-width="3"/><path d="M30 13v4M28 15h4M33 19v3M31.5 20.5h3" stroke="#8fae5a" stroke-width="1.5"/></svg>
    <div class="feature-name">Simple Integration</div>
    <p class="feature-text">Our API, based on REST and JSON, is as simple as they come. Plus, we have <a href="#">great documentation</a>.</p>
  </div>
  <div class="feature" style="left:794px">
    <svg class="feature-icon" width="46" height="46" viewBox="0 0 46 46"><circle cx="23" cy="23" r="22" fill="#333"/><circle cx="23" cy="23" r="19" fill="none" stroke="#fff" stroke-width="1.5"/><circle cx="23" cy="23" r="8" fill="none" stroke="#8fae5a" stroke-width="2"/><path d="M23 18v9M19.5 23.5l3.5 3.5 3.5-3.5" fill="none" stroke="#8fae5a" stroke-width="2"/></svg>
    <div class="feature-name">Lots of Space</div>
    <p class="feature-text">Our plans range from 1,000 to 250,000 Zip files. Need unlimited downloads? We got that. Check out our <a href="#">plans.</a></p>
  </div>

  <h2 class="section-title tryit-title"><span class="brace">{</span> Try It <span class="brace">}</span></h2>
  <p class="tryit-intro">The demo below lets a user instantly download a custom Zip file containing just the images they want. Try it out, then check out the code behind it.</p>
  <div class="demo-frame"></div>
</div>
</body>
</html>
```